Ward Compass Business Card Design*

We need a business card design for our company Ward Compass. Our company is specialized in providing online consulting services regarding medical institutions, hospitals and doctors. We work with patients worldwide looking to choose between healthcare providers. We have a website you may use as a reference, where we list doctors and clinics worldwide. So we target Medical providers as well as patients worldwide.
Target Market(s)
Medical Providers and patients around the world
Industry/Entity Type
Medical
Contact Information for Business Card
Salwa Kettani
CEO
+90 612 348 2175
info@wardcompass.example
www.wardcompass.example
14 Annakhil 7 H.R.B. Rabat, Morocco
Requirements
Must have
- Company logo/name on one full side, personal info and smaller logo and company name on the other side.
Nice to have
- Smart and elegant design

```html
<!DOCTYPE html>
<html lang="en">
<head>
<meta charset="utf-8">
<title>Ward Compass Business Card</title>
<link rel="stylesheet" href="https://fonts.googleapis.com/css2?family=Lato:wght@400;700&family=Raleway:wght@500&display=swap">
<style>
  :root {
    --backdrop: #404040;
    --card-white: #ffffff;
    --brand-blue: #3176b5;
    --deep-blue: #2a6bae;
    --sky-blue: #2fa3d9;
    --ink: #1e1e1e;
  }
  * { box-sizing: border-box; margin: 0; padding: 0; }
  html, body {
    width: 1200px;
    height: 900px;
    overflow: hidden;
    background: var(--backdrop);
  }
  .canvas {
    position: relative;
    width: 1200px;
    height: 900px;
  }
  .card {
    position: absolute;
    top: 200px;
    width: 310px;
    height: 502px;
  }
  .card--front {
    left: 253px;
    background: var(--card-white);
    border-radius: 62px 0 62px 0;
  }
  .card--back {
    left: 627px;
    background: var(--brand-blue);
    border-radius: 0 62px 0 62px;
  }
  .brand-dot {
    position: absolute;
    left: 125px;
    top: 90px;
    width: 60px;
    height: 60px;
    border-radius: 50%;
    background: var(--sky-blue);
  }
  .brand-name {
    position: absolute;
    left: 0;
    width: 100%;
    text-align: center;
    font-family: "Raleway", sans-serif;
    font-weight: 500;
    letter-spacing: 0.5px;
    text-transform: uppercase;
  }
  .card--front .brand-name {
    top: 198px;
    font-size: 29px;
    color: var(--deep-blue);
  }
  .card--back .brand-name {
    top: 230px;
    font-size: 32px;
    color: var(--card-white);
  }
  .person {
    position: absolute;
    left: 33px;
    top: 336px;
    font-family: "Lato", sans-serif;
  }
  .person__name {
    font-size: 17px;
    line-height: 20px;
    text-transform: uppercase;
    color: var(--sky-blue);
  }
  .person__name strong {
    font-weight: 700;
    color: var(--deep-blue);
  }
  .person__role {
    font-size: 14px;
    line-height: 17px;
    color: var(--ink);
  }
  .contact-list {
    position: absolute;
    left: 33px;
    top: 398px;
    list-style: none;
    font-family: "Lato", sans-serif;
    font-size: 14px;
    line-height: 18.5px;
    color: var(--ink);
  }
  .contact-list li {
    display: flex;
    align-items: center;
    gap: 3px;
  }
  .contact-icon {
    width: 13px;
    height: 13px;
    flex: none;
    fill: var(--sky-blue);
  }
</style>
</head>
<body>
<main class="canvas">
  <section class="card card--front" aria-label="Business card, personal side">
    <span class="brand-dot" aria-hidden="true"></span>
    <p class="brand-name">Ward Compass</p>
    <div class="person">
      <p class="person__name"><strong>Salwa</strong> Kettani</p>
      <p class="person__role">CEO</p>
    </div>
    <ul class="contact-list">
      <li>
        <svg class="contact-icon" viewBox="0 0 16 16" aria-hidden="true"><path d="M1 5c0-2 2-3 7-3s7 1 7 3v1h-4V4.5H5V6H1zM4 7h8l2 6H2z"/></svg>
        +90 612 348 2175
      </li>
      <li>
        <svg class="contact-icon" viewBox="0 0 16 16" aria-hidden="true"><path d="M1 3h14v10H1z"/><path d="M1.5 3.5 8 9l6.5-5.5" fill="none" stroke="#fff" stroke-width="1.3"/></svg>
        info@wardcompass.example
      </li>
      <li>
        <svg class="contact-icon" viewBox="0 0 16 16" aria-hidden="true"><circle cx="8" cy="8" r="7"/><path d="M4 5c2 0 2 2 4 2s1 3-1 4M10 3c1 1 3 2 2 4" fill="none" stroke="#fff" stroke-width="1.2"/></svg>
        www.wardcompass.example
      </li>
    </ul>
  </section>

  <section class="card card--back" aria-label="Business card, brand side">
    <p class="brand-name">Ward Compass</p>
  </section>
</main>
</body>
</html>
```